AI Business Tools Landing Page

My web-based website builder (Pavlora.com) will be adding many new features in the very near future and I need an eye-catching landing page to promote these new products.

The page will have a primary section of the 8 main products we are promoting:
1. AI Instant Website Generator
2. AI Chatbot
3. Online Store Builder with AI Assistance
4. AI Auto-Blogging System
5. Online Scheduling System
6. Custom Email System
7. SEO Service
8. CRM System

The page will also have a smaller section for links to our affiliate programs. These can be smaller, less-promanent buttons or links. These are the affiliate products:
1. Get Your LLC
2. Website Design and Maintenance
3. Searchly Ads Management
4. Social Media Posting Service
5. Logo Design
6. Trademark Registration
7. Patent Application
8. Printing Services (including postcards, flyers, and merch.)
9. Bulk AI Content Generator

The theme and color scheme of the page should follow the theme of our main website, which is https://pavlora.com.

I need the page fully coded and ready to deploy on my server.

I look forward to seeing your amazing designs!

```html
<!DOCTYPE html>
<html lang="en">
<head>
<meta charset="UTF-8">
<title>Pavlora – Additional Features &amp; Growth Tools</title>
<link href="https://fonts.googleapis.com/css2?family=Fira+Sans:wght@400;500;600;700&display=swap" rel="stylesheet">
<style>
  :root {
    --navy: #1b3a52;
    --ink: #222a30;
    --text: #3a3f44;
    --accent: #1f8fd6;
    --accent-dark: #1765a8;
    --card-border: #9fd8ee;
    --white: #ffffff;
  }
  * { box-sizing: border-box; margin: 0; padding: 0; }
  html, body { width: 1075px; height: 1200px; overflow: hidden; background: var(--white); }
  body { position: relative; font-family: "Fira Sans", sans-serif; color: var(--text); }

  .site-header {
    position: absolute; left: 0; top: 0; width: 1075px; height: 78px;
    background: var(--navy); border-bottom-left-radius: 78px;
    display: flex; align-items: center; justify-content: center; gap: 12px;
  }
  .brand { display: flex; align-items: center; gap: 12px; color: var(--white); font-weight: 600; font-size: 31px; letter-spacing: .3px; }
  .brand-mark { width: 26px; height: 26px; border-radius: 50%; background: var(--accent); }

  .section-title {
    position: absolute; left: 0; width: 1075px; text-align: center;
    font-weight: 700; font-size: 38px; line-height: 44px; color: var(--ink);
  }
  .title-features { top: 122px; }
  .title-tools { top: 568px; }

  .divider { position: absolute; left: 472px; width: 132px; height: 20px; }
  .divider-features { top: 181px; }
  .divider-tools { top: 670px; }

  .feature-grid {
    position: absolute; left: 101px; top: 233px; width: 874px;
    display: grid; grid-template-columns: repeat(3, 280px); grid-auto-rows: 80px; gap: 19px 17px;
  }
  .feature-card {
    display: flex; align-items: center; gap: 16px; padding: 0 20px 0 24px;
    border: 1.5px solid var(--card-border); border-radius: 5px; background: var(--white);
    box-shadow: 0 2px 6px rgba(27, 58, 82, .08);
    font-size: 15.5px; line-height: 21px;
  }
  .feature-card .icon { flex: 0 0 46px; width: 46px; height: 46px; }
  .feature-card .note { font-size: 10.5px; }

  .tool-grid {
    position: absolute; left: 101px; top: 723px; width: 874px;
    display: grid; grid-template-columns: repeat(4, 200px); grid-auto-rows: 129px; gap: 21px 24.6px;
  }
  .tool-card {
    display: flex; flex-direction: column; align-items: center; justify-content: flex-start;
    padding-top: 18px; text-align: center;
    border: 1.5px solid var(--card-border); border-radius: 5px; background: var(--white);
    box-shadow: 0 2px 6px rgba(27, 58, 82, .08);
    font-size: 15.5px; line-height: 21.5px;
  }
  .tool-card .icon { width: 44px; height: 44px; margin-bottom: 11px; }

  .icon { fill: none; stroke: var(--accent-dark); stroke-width: 1.6; stroke-linecap: round; stroke-linejoin: round; }
  .icon .hl { stroke: var(--accent); }

  .site-footer {
    position: absolute; left: 0; top: 1062px; width: 1075px; height: 138px; background: var(--navy);
  }
  .footer-brand { position: absolute; left: 104px; top: 50px; font-size: 27px; }
  .footer-brand .brand-mark { width: 30px; height: 30px; }
  .social-links {
    position: absolute; left: 447px; top: 36px; width: 180px;
    display: grid; grid-template-columns: repeat(5, 22px); gap: 16px 17px;
  }
  .social-links span { width: 22px; height: 22px; border-radius: 50%; background: var(--white); display: block; }
  .copyright { position: absolute; right: 102px; top: 56px; color: var(--white); font-size: 13px; }
</style>
</head>
<body>

<header class="site-header">
  <div class="brand"><span class="brand-mark"></span>Pavlora</div>
</header>

<h1 class="section-title title-features">Additional Features for Your Website</h1>
<svg class="divider divider-features" viewBox="0 0 132 20"><line x1="0" y1="10" x2="45" y2="10" stroke="#1f8fd6" stroke-width="1.5"/><circle cx="66" cy="10" r="8" fill="#1f8fd6"/><line x1="87" y1="10" x2="132" y2="10" stroke="#1f8fd6" stroke-width="1.5"/></svg>

<section class="feature-grid">
  <div class="feature-card">
    <svg class="icon" viewBox="0 0 46 46"><rect x="10" y="6" width="20" height="32"/><path d="M14 12h4M22 12h4M14 18h4M22 18h4M14 24h4"/><circle class="hl" cx="31" cy="30" r="4"/><path class="hl" d="M24 41c0-5 3-7 7-7s7 2 7 7"/></svg>
    <span>Get Your LLC</span>
  </div>
  <div class="feature-card">
    <svg class="icon" viewBox="0 0 46 46"><rect x="3" y="7" width="40" height="27" rx="2"/><path d="M18 40h10M23 34v6"/><path class="hl" d="M8 24l6-6 6 6v6H8z"/><path d="M26 14h12M26 20h12M26 26h12"/></svg>
    <span>Website Design and<br>Maintenance</span>
  </div>
  <div class="feature-card">
    <svg class="icon" viewBox="0 0 46 46"><path d="M19 8l16 28M27 8L11 36"/><circle class="hl" cx="10" cy="34" r="5"/><circle cx="36" cy="34" r="5"/></svg>
    <span>Searchly Ads<br>Management</span>
  </div>
  <div class="feature-card">
    <svg class="icon" viewBox="0 0 46 46"><rect x="3" y="10" width="32" height="30" rx="2"/><path d="M3 16h32"/><rect x="9" y="22" width="20" height="13"/><circle class="hl" cx="36" cy="10" r="7"/><path class="hl" d="M33 11h2v4h-2zM35 11l2-4 2 1v6"/></svg>
    <span>Social Media Posting<br>Service</span>
  </div>
  <div class="feature-card">
    <svg class="icon" viewBox="0 0 46 46"><rect x="4" y="4" width="34" height="34" rx="6"/><path class="hl" d="M14 10v20h10"/><path d="M26 30l8 8 4-4-8-8z"/></svg>
    <span>Logo Design</span>
  </div>
  <div class="feature-card">
    <svg class="icon" viewBox="0 0 46 46"><circle cx="23" cy="23" r="18"/><path class="hl" d="M18 32V14h6a5 5 0 010 10h-6M24 24l6 8"/></svg>
    <span>Trademark Registration</span>
  </div>
  <div class="feature-card">
    <svg class="icon" viewBox="0 0 46 46"><rect x="6" y="6" width="28" height="36" rx="2"/><rect x="14" y="3" width="12" height="6"/><path d="M11 16h3M18 16h10M11 23h3M18 23h10M11 30h3M18 30h8"/><path class="hl" d="M36 28l7 3v5c0 4-3 6-7 8-4-2-7-4-7-8v-5z"/></svg>
    <span>Patent Application</span>
  </div>
  <div class="feature-card">
    <svg class="icon" viewBox="0 0 46 46"><path d="M4 8l19 4 19-4v30l-19 4-19-4z"/><path d="M23 12v30"/><path class="hl" d="M8 24l4-6 4 5 3-3"/><path d="M27 18h11M27 24h11M27 30h11"/></svg>
    <span>Printing Services <span class="note">(including<br>postcards, flyers, and merch.)</span></span>
  </div>
  <div class="feature-card">
    <svg class="icon" viewBox="0 0 46 46"><rect x="3" y="8" width="40" height="30" rx="2"/><path d="M3 14h40"/><path d="M8 20h4v4H8zM8 28h4v4H8zM16 20h14M16 26h14M16 32h10"/><rect class="hl" x="32" y="24" width="9" height="9" rx="2"/></svg>
    <span>Bulk AI Content<br>Generator</span>
  </div>
</section>

<h2 class="section-title title-tools">More Tools to Help You Grow<br>Your Business</h2>
<svg class="divider divider-tools" viewBox="0 0 132 20"><line x1="0" y1="10" x2="45" y2="10" stroke="#1f8fd6" stroke-width="1.5"/><circle cx="66" cy="10" r="8" fill="#1f8fd6"/><line x1="87" y1="10" x2="132" y2="10" stroke="#1f8fd6" stroke-width="1.5"/></svg>

<section class="tool-grid">
  <div class="tool-card">
    <svg class="icon" viewBox="0 0 44 44"><rect x="2" y="4" width="40" height="32" rx="2"/><path d="M2 10h40"/><rect class="hl" x="7" y="15" width="13" height="11"/><circle cx="30" cy="22" r="3"/><rect x="25" y="27" width="10" height="8"/></svg>
    <span>AI Instant Website<br>Generator</span>
  </div>
  <div class="tool-card">
    <svg class="icon" viewBox="0 0 44 44"><rect x="2" y="4" width="40" height="32" rx="2"/><path d="M2 10h40"/><path class="hl" d="M24 16h14v12h-8l-4 4v-4h-2z"/></svg>
    <span>AI ChatBot</span>
  </div>
  <div class="tool-card">
    <svg class="icon" viewBox="0 0 44 44"><rect x="2" y="4" width="40" height="34" rx="2"/><path d="M2 10h40"/><rect x="7" y="15" width="8" height="7"/><rect x="7" y="26" width="8" height="7"/><rect x="24" y="15" width="8" height="7"/><path class="hl" d="M20 24v10l3-2 3 5 2-1-3-5h4z"/></svg>
    <span>Online Store Builder<br>with AI Assistance</span>
  </div>
  <div class="tool-card">
    <svg class="icon" viewBox="0 0 44 44"><rect x="2" y="2" width="40" height="40" rx="2"/><path d="M2 8h40"/><rect class="hl" x="8" y="14" width="12" height="14"/><rect x="24" y="14" width="12" height="14"/><path d="M8 34h28"/></svg>
    <span>AI Auto-Blogging<br>System</span>
  </div>
  <div class="tool-card">
    <svg class="icon" viewBox="0 0 44 44"><rect x="3" y="6" width="36" height="32" rx="2"/><path d="M3 13h36M12 3v6M30 3v6M9 19h24M9 25h24M9 31h20M15 17v18M21 17v18M27 17v18"/><circle class="hl" cx="36" cy="36" r="6"/><path class="hl" d="M33 36l2 2 4-4"/></svg>
    <span>Online Scheduling<br>System</span>
  </div>
  <div class="tool-card">
    <svg class="icon" viewBox="0 0 44 44"><rect x="2" y="3" width="40" height="30" rx="2"/><path d="M16 40h12M22 33v7"/><rect class="hl" x="11" y="11" width="22" height="14"/><path class="hl" d="M11 11l11 8 11-8"/></svg>
    <span>Custom emails using<br>your domain</span>
  </div>
  <div class="tool-card">
    <svg class="icon" viewBox="0 0 44 44"><rect x="2" y="8" width="40" height="26" rx="2"/><path d="M16 40h12M22 34v6M2 28h40"/><circle class="hl" cx="22" cy="16" r="7"/><path class="hl" d="M22 5v3M22 24v3M11 16h3M30 16h3"/></svg>
    <span>SEO Service – Automatic<br>Backlink Building</span>
  </div>
  <div class="tool-card">
    <svg class="icon" viewBox="0 0 44 44"><path d="M10 38v-6a12 12 0 1112-12"/><circle class="hl" cx="30" cy="14" r="6"/><path class="hl" d="M30 4v3M30 21v3M20 14h3M37 14h3"/><path d="M4 8l3 2M6 2l2 3"/></svg>
    <span>Customer Relationship<br>Management (System)</span>
  </div>
</section>

<footer class="site-footer">
  <div class="brand footer-brand"><span class="brand-mark"></span>Pavlora</div>
  <nav class="social-links" aria-label="Social links">
    <span></span><span></span><span></span><span></span><span></span>
    <span></span><span></span><span></span><span></span><span></span>
  </nav>
  <p class="copyright">2024 Pavlora. All Rights Reserved.</p>
</footer>

</body>
</html>
```